Every Shelf Set Neatly or ESN Organized needs a business card design. ESN Organized is a professi

We need a business card design that is clean, sharp and conveys a sense of organization. I already have a logo.

Target Market(s)

Families (specifically mothers), small business owners, parents, seniors

Industry/Entity Type

Business

Contact Information for Business Card

My website is www.esnorganized-example.com and my Facebook page is http://www.sociallink-example.com/everyshelfsetneatly. The phone number is 418-552-7094 and I want to be listed as Lorna M. Pelham, Owner

Requirements
Must have
• My logo.

```html
<!DOCTYPE html>
<html lang="en">
<head>
<meta charset="utf-8">
<title>Every Shelf Set Neatly – Business Card</title>
<link rel="stylesheet" href="https://fonts.googleapis.com/css2?family=Lato:ital,wght@0,400;0,700;0,900;1,400&display=swap">
<style>
  :root {
    --page-bg: #d9dcdf;
    --card-top: #f1f2f3;
    --card-bottom: #e3e5e7;
    --ink: #1d1f22;
    --ink-soft: #2b2d30;
    --brand-blue: #1c3f94;
    --band-black: #0b0c0e;
    --band-blue: #1f4fa8;
    --band-blue-dark: #0f2a66;
  }
  * { box-sizing: border-box; margin: 0; padding: 0; }
  html, body {
    width: 1200px; height: 970px; overflow: hidden;
    background: var(--page-bg);
    font-family: "Lato", Arial, sans-serif;
  }
  .business-card {
    position: absolute; left: 100px; top: 185px;
    width: 1000px; height: 600px;
    background: linear-gradient(180deg, var(--card-top), var(--card-bottom));
    box-shadow: 0 10px 30px rgba(0,0,0,0.18);
    overflow: hidden;
  }
  .brand-lockup {
    position: absolute; left: 0; right: 0; top: 100px;
    display: flex; justify-content: center; align-items: center; gap: 18px;
  }
  .brand-square {
    width: 44px; height: 44px; background: var(--brand-blue); flex: none;
  }
  .brand-name {
    font-size: 46px; font-weight: 400; letter-spacing: 5px;
    color: var(--ink); line-height: 1;
  }
  .tagline {
    position: absolute; left: 0; right: 0; top: 182px;
    text-align: center;
    font-size: 24px; font-style: italic; color: var(--ink-soft);
  }
  .contact-list {
    position: absolute; left: 60px; top: 366px;
    list-style: none;
  }
  .contact-item {
    display: flex; align-items: center; gap: 14px;
    height: 50px; font-size: 24px; color: var(--ink-soft);
  }
  .contact-icon { width: 36px; height: 36px; flex: none; }
  .website {
    position: absolute; left: 64px; top: 480px;
    font-size: 21px; font-weight: 700; letter-spacing: 6px;
    color: var(--brand-blue);
  }
  .owner {
    position: absolute; right: 59px; top: 408px; text-align: right;
  }
  .owner-name {
    font-size: 34px; font-weight: 900; color: var(--brand-blue); line-height: 1.2;
  }
  .owner-title {
    font-size: 26px; font-style: italic; color: var(--ink); margin-top: 4px;
  }
  .band-black {
    position: absolute; left: 0; right: 0; top: 553px; height: 14px;
    background: var(--band-black);
  }
  .band-blue {
    position: absolute; left: 0; right: 0; top: 567px; height: 33px;
    background: linear-gradient(90deg, var(--band-blue), var(--band-blue-dark));
  }
</style>
</head>
<body>
  <div class="business-card">
    <div class="brand-lockup">
      <span class="brand-square" aria-hidden="true"></span>
      <span class="brand-name">Every Shelf Set Neatly</span>
    </div>
    <p class="tagline">Calm, clear spaces for every room, every season, every day</p>

    <ul class="contact-list">
      <li class="contact-item">
        <svg class="contact-icon" viewBox="0 0 36 36" aria-hidden="true">
          <circle cx="18" cy="18" r="18" fill="var(--brand-blue)"/>
          <path d="M12.5 10.5c1-.8 2.2-.6 2.8.4l1.6 2.6c.5.9.3 1.9-.5 2.5l-1 .8c.8 1.9 2.3 3.6 4.2 4.6l.9-.9c.7-.7 1.7-.8 2.5-.2l2.5 1.8c.9.7 1 1.9.2 2.8l-1 1.1c-1 1.1-2.6 1.4-4 .8-4.3-1.8-7.6-5.3-9.2-9.7-.5-1.4-.1-2.9 1-3.9z" fill="#fff"/>
        </svg>
        <span>418-552-7094</span>
      </li>
      <li class="contact-item">
        <svg class="contact-icon" viewBox="0 0 36 36" aria-hidden="true">
          <circle cx="18" cy="18" r="18" fill="var(--brand-blue)"/>
        </svg>
        <span>sociallink-example.com/everyshelfsetneatly</span>
      </li>
    </ul>
    <div class="website">www.esnorganized-example.com</div>

    <div class="owner">
      <div class="owner-name">Lorna M. Pelham</div>
      <div class="owner-title">Owner</div>
    </div>

    <div class="band-black"></div>
    <div class="band-blue"></div>
  </div>
</body>
</html>
```